Upmarket Dessert Lounge needs a Business Card Design

We are an upmarket dessert lounge needing a business card to match our image.

We want something that is simple yet beautiful, feminine, classy, sophisticated and elegant. We want it to stand out and don't mind if it is bold.

The design should include our logo and colours of red or maroon with gold highlights. We don't mind if black is used.

Marlow & Quince

Target Market(s)

For those who like to indulge or treat themselves and give in to their temptations on good quality desserts.

Industry/Entity Type

Business

Requirements
Must have
• Must include our logo and our name

Marlow & Quince

M & Q

```html
<!DOCTYPE html>
<html lang="en">
<head>
<meta charset="utf-8">
<title>Marlow &amp; Quince — Business Card</title>
<link rel="stylesheet" href="https://fonts.googleapis.com/css2?family=Libre+Baskerville:wght@400;700&family=Open+Sans:wght@400&display=swap">
<style>
  :root {
    --maroon: #7a1519;
    --maroon-deep: #5e0f12;
    --peach: #f8cf9c;
    --card: #ffffff;
    --ink: #2f2f2f;
    --backdrop: #ece8e3;
  }
  * { box-sizing: border-box; margin: 0; padding: 0; }
  html, body { width: 1200px; height: 758px; overflow: hidden; }
  body {
    background: var(--backdrop);
    font-family: "Open Sans", Arial, sans-serif;
    color: var(--ink);
    position: relative;
  }
  .card {
    position: absolute;
    top: 229px;
    width: 525px;
    height: 300px;
    background: var(--card);
    border-radius: 20px;
    box-shadow: 0 10px 28px rgba(0,0,0,0.18);
    overflow: hidden;
  }
  .card--front { left: 50px; }
  .card--back { left: 625px; }

  .brand-name {
    position: absolute;
    left: 0; right: 0;
    top: 62px;
    text-align: center;
    font-family: "Libre Baskerville", "Times New Roman", serif;
    font-weight: 400;
    font-size: 30px;
    letter-spacing: 1px;
    color: var(--maroon);
  }

  .name-band {
    position: absolute;
    left: 0;
    top: 150px;
    width: 470px;
    height: 46px;
    background: var(--maroon);
  }
  .name-band__accent {
    position: absolute;
    left: 474px;
    top: 150px;
    width: 30px;
    height: 30px;
    background: var(--peach);
  }
  .name-band__text {
    position: absolute;
    right: 22px;
    bottom: 6px;
    color: #fff;
    font-family: "Libre Baskerville", "Times New Roman", serif;
    font-size: 17px;
    font-weight: 700;
    white-space: nowrap;
  }
  .name-band__text .title { font-family: "Open Sans", Arial, sans-serif; font-weight: 400; font-size: 13px; }

  .contact {
    position: absolute;
    left: 0; right: 0;
    font-size: 13px;
    color: var(--ink);
    display: flex;
    justify-content: center;
    gap: 22px;
    white-space: nowrap;
  }
  .contact span { display: inline-flex; align-items: center; gap: 5px; }
  .contact svg { width: 12px; height: 12px; fill: var(--ink); }
  .contact--row1 { top: 212px; }
  .contact--row2 { top: 236px; }
  .contact--address { top: 262px; font-size: 14px; }

  .monogram {
    position: absolute;
    left: 0; right: 0;
    top: 70px;
    text-align: center;
    font-family: "Libre Baskerville", "Times New Roman", serif;
    font-size: 76px;
    font-weight: 400;
    color: var(--maroon);
    line-height: 1;
  }
  .back-web {
    position: absolute;
    left: 0; right: 0;
    top: 212px;
    text-align: center;
    font-size: 20px;
    letter-spacing: 3px;
    color: var(--ink);
  }
</style>
</head>
<body>
  <section class="card card--front" aria-label="Business card front">
    <div class="brand-name">Marlow &amp; Quince</div>

    <div class="name-band">
      <div class="name-band__text">Your name, <span class="title">Title</span></div>
    </div>
    <div class="name-band__accent"></div>

    <div class="contact contact--row1">
      <span>
        <svg viewBox="0 0 24 24" aria-hidden="true"><path d="M6.6 10.8a15 15 0 0 0 6.6 6.6l2.2-2.2a1 1 0 0 1 1-.25 11.4 11.4 0 0 0 3.6.57 1 1 0 0 1 1 1V20a1 1 0 0 1-1 1A17 17 0 0 1 3 4a1 1 0 0 1 1-1h3.5a1 1 0 0 1 1 1c0 1.25.2 2.45.57 3.57a1 1 0 0 1-.25 1z"/></svg>
        555-201-4870
      </span>
      <span>
        <svg viewBox="0 0 24 24" aria-hidden="true"><path d="M8 1h8a2 2 0 0 1 2 2v18a2 2 0 0 1-2 2H8a2 2 0 0 1-2-2V3a2 2 0 0 1 2-2zm0 3v14h8V4zm4 15.5a1 1 0 1 0 0 2 1 1 0 0 0 0-2z"/></svg>
        555-201-4870
      </span>
      <span>
        <svg viewBox="0 0 24 24" aria-hidden="true"><path d="M2 5h20v14H2zm2 2v.5l8 5 8-5V7zm0 2.8V17h16V9.8l-8 5z"/></svg>
        info@marlowquince.com
      </span>
    </div>
    <div class="contact contact--row2">
      <span>
        <svg viewBox="0 0 24 24" aria-hidden="true"><path d="M12 2a10 10 0 1 0 0 20 10 10 0 0 0 0-20zm6.9 6h-2.8a15 15 0 0 0-1.3-3.6A8 8 0 0 1 18.9 8zM12 4c.8 1.2 1.5 2.5 1.9 4h-3.8c.4-1.5 1.1-2.8 1.9-4zM4.3 14a8 8 0 0 1 0-4h3.4a16 16 0 0 0 0 4zm.8 2h2.8c.3 1.3.8 2.5 1.3 3.6A8 8 0 0 1 5.1 16zm2.8-8H5.1a8 8 0 0 1 4.1-3.6C8.7 5.5 8.2 6.7 7.9 8zM12 20c-.8-1.2-1.5-2.5-1.9-4h3.8c-.4 1.5-1.1 2.8-1.9 4zm2.3-6H9.7a14 14 0 0 1 0-4h4.6a14 14 0 0 1 0 4zm.5 5.6c.5-1.1 1-2.3 1.3-3.6h2.8a8 8 0 0 1-4.1 3.6zm1.5-5.6a16 16 0 0 0 0-4h3.4a8 8 0 0 1 0 4z"/></svg>
        www.marlowquince.com
      </span>
    </div>
    <div class="contact contact--address">
      <span>Street Name, City Name, State Zip Code</span>
    </div>
  </section>

  <section class="card card--back" aria-label="Business card back">
    <div class="monogram">M &amp; Q</div>
    <div class="back-web">www.marlowquince.com</div>
  </section>
</body>
</html>
```